New Web Design Project

Number of Pages Required

1 page

Requirements
Must have
• An Overview / Background of the Business & Services(not for profit rescue animal farm)
• The Target Market / Audience you are trying to reach (animal lovers)
• Design Specifics; any preferences or ideas for Style, Colour, Imagery, etc (no preferences)

```html
<!DOCTYPE html>
<html lang="en">
<head>
<meta charset="utf-8">
<title>Maple Hollow Farms</title>
<link href="https://fonts.googleapis.com/css2?family=Montserrat:wght@400;500;600;700&family=Open+Sans:wght@400;600&display=swap" rel="stylesheet">
<style>
:root{
  --green:#5c820a;
  --green-dark:#4d6e08;
  --ink:#1c1c1c;
  --text:#333;
  --light:#f1f1f1;
  --footer:#efefef;
  --white:#fff;
  --black:#111;
}
*{box-sizing:border-box;margin:0;padding:0}
html,body{width:1200px;height:2568px;overflow:hidden;background:var(--white)}
body{position:relative;font-family:'Open Sans',sans-serif;color:var(--text)}
.abs{position:absolute}
.site-header{position:absolute;left:0;top:0;width:1200px;height:102px;background:var(--white)}
.brand{position:absolute;left:113px;top:38px;font:700 29px/1 'Montserrat',sans-serif;color:var(--ink)}
.nav a{position:absolute;top:42px;font:500 15px/1 'Montserrat',sans-serif;color:var(--ink);text-decoration:none}
.nav a.active::after{content:"";position:absolute;left:0;right:0;top:55px;height:2px;background:var(--green)}
.search{position:absolute;left:1048px;top:31px;width:40px;height:40px;border:2px solid #2b6cb0;border-radius:50%}
.hero{position:absolute;left:0;top:102px;width:1200px;height:569px;background:linear-gradient(180deg,#2f4a1e 0%,#4d6f2a 45%,#6f9b32 75%,#547a25 100%)}
.hero-panel{position:absolute;left:231px;top:258px;width:740px;height:205px;background:rgba(20,25,15,.45);text-align:center;color:var(--white)}
.hero-panel h1{font:700 38px/1 'Montserrat',sans-serif;margin-top:24px}
.hero-panel p{font-size:15px;line-height:25.5px;margin:16px 30px 0}
.btn{position:absolute;display:block;border-radius:21px;background:var(--green);color:var(--white);font:700 14px/40px 'Montserrat',sans-serif;text-align:center;text-transform:uppercase}
.section-title{position:absolute;left:0;width:1200px;text-align:center;font-family:'Montserrat',sans-serif;font-weight:700;color:var(--ink)}
.welcome-text{position:absolute;left:118px;top:782px;width:964px;text-align:center;font-size:16px;line-height:26px;color:var(--text)}
.gallery{position:absolute;left:0;top:1019px;width:1200px;height:835px;background:var(--light)}
.tile{position:absolute;width:308px;height:264px}
.tile-label{position:absolute;left:0;right:0;top:118px;text-align:center;color:var(--white);font:700 21px/1 'Montserrat',sans-serif}
.join{position:absolute;left:0;top:1854px;width:1200px;height:329px;background:var(--green)}
.email{position:absolute;left:313px;top:123px;width:574px;height:45px;background:var(--white);font:600 14px/45px 'Montserrat',sans-serif;color:var(--ink);padding-left:28px}
.footer{position:absolute;left:0;top:2183px;width:1200px;height:299px;background:var(--footer)}
.foot-head{position:absolute;top:43px;font:500 15px/1 'Montserrat',sans-serif;color:var(--ink);text-transform:uppercase}
.foot-link{position:absolute;left:137px;font-size:14.5px;color:var(--ink)}
.contact-item{position:absolute;left:377px;font-size:14.5px;line-height:17px;color:var(--ink)}
.map{position:absolute;left:616px;top:44px;width:497px;height:223px;background:linear-gradient(135deg,#eceae4,#dcdcd6);border:1px solid #cfcfcf;box-shadow:0 1px 4px rgba(0,0,0,.2)}
.bottom-bar{position:absolute;left:0;top:2482px;width:1200px;height:76px;background:var(--footer);border-top:1px solid #ddd}
.social{position:absolute;top:24px;width:34px;height:34px;border:2px solid var(--ink);border-radius:50%}
.copyright{position:absolute;left:860px;top:30px;font-size:14.5px;color:var(--ink)}
.base-line{position:absolute;left:0;top:2558px;width:1200px;height:10px;background:var(--green)}
</style>
</head>
<body>

<header class="site-header">
  <div class="brand">Maple Hollow Farms</div>
  <nav class="nav">
    <a class="active" style="left:587px">Home</a>
    <a style="left:662px">About Us</a>
    <a style="left:760px">Gallery</a>
    <a style="left:842px">Locations</a>
    <a style="left:942px">Contact Us</a>
  </nav>
  <div class="search">
    <svg width="36" height="36" viewBox="0 0 36 36"><circle cx="17" cy="17" r="4.5" fill="none" stroke="#2b6cb0" stroke-width="2"/><line x1="20.2" y1="20.2" x2="23" y2="23" stroke="#2b6cb0" stroke-width="2.2" stroke-linecap="round"/></svg>
  </div>
</header>

<section class="hero" role="img" aria-label="Sheep grazing in a shaded green woodland pasture behind a wooden fence">
  <div class="hero-panel">
    <h1>Maple Hollow Farms</h1>
    <p>Lorem Ipsum is simply dummy text of the printing and typesetting industry. Lorem Ipsum has been the industry's standard dummy text ever since the 1500s, when an unknown printer took a galley of type and scrambled</p>
  </div>
  <a class="btn" style="left:532px;top:437px;width:136px">Read More</a>
</section>

<h2 class="section-title" style="top:719px;font-size:40px;font-weight:600">Welcome To Maple Hollow Farms</h2>
<p class="welcome-text">Lorem ipsum dolor sit amet, consectetur adipiscing elit, sed do eiusmod tempor incididunt ut labore et dolore magna aliqua. Ut enim ad minim veniam, quis nostrud exercitation ullamco laboris nisi ut aliquip ex ea commodo consequat. Duis aute irure dolor in reprehenderit in voluptate velit esse cillum dolore eu fugiat nulla pariatur. Excepteur sint occaecat cupidatat non proident, sunt in culpa qui officia deserunt mollit anim id est laborum.</p>
<a class="btn" style="left:532px;top:904px;width:136px">Read More</a>

<section class="gallery">
  <h2 class="section-title" style="top:62px;font-size:29px">OUR GALLERY</h2>
  <div class="tile" style="left:111px;top:131px;background:linear-gradient(180deg,#6f8a4a,#b9b29a 55%,#5f7a3a)" role="img" aria-label="Flock of sheep grazing on a grassy hillside"></div>
  <div class="tile" style="left:445px;top:131px;background:linear-gradient(180deg,#bfc6cc 0%,#8c9690 40%,#3f4f30 70%,#2f3d24)" role="img" aria-label="Sheep in a fenced field under tall trees"><span class="tile-label">HOLLOW FARM</span></div>
  <div class="tile" style="left:777px;top:131px;background:linear-gradient(180deg,#4f6a46 0%,#7d9566 35%,#8e8a4c 65%,#6d6a36)" role="img" aria-label="Horses grazing in a valley pasture"></div>
  <div class="tile" style="left:111px;top:419px;background:linear-gradient(180deg,#6b6d70 0%,#d9c8a2 40%,#7c6548 65%,#4a3a28)" role="img" aria-label="Cattle grazing at sunset under a cloudy sky"></div>
  <div class="tile" style="left:445px;top:419px;background:linear-gradient(180deg,#8d9aa8 0%,#c2c9cf 35%,#7a5a4a 50%,#5b7a3e 75%,#4c6a34)" role="img" aria-label="Red barn with goats in a fenced yard"></div>
  <div class="tile" style="left:777px;top:419px;background:linear-gradient(180deg,#efe7d3 0%,#e9b94a 40%,#b7782a 65%,#5a3a1c)" role="img" aria-label="Cows grazing in golden morning haze"></div>
  <a class="btn" style="left:519px;top:726px;width:162px">View More</a>
</section>

<section class="join">
  <h2 class="section-title" style="top:56px;font-size:30px;color:var(--white)">JOIN WITH US</h2>
  <div class="email">ENTER EMAIL ID
    <svg class="abs" style="left:530px;top:15px" width="16" height="14" viewBox="0 0 16 14"><rect x="1" y="2" width="14" height="10" fill="none" stroke="#222" stroke-width="1.5"/><polyline points="1,2 8,8 15,2" fill="none" stroke="#222" stroke-width="1.5"/></svg>
  </div>
  <a class="btn" style="left:519px;top:194px;width:162px;background:var(--black)">Subscribe</a>
</section>

<footer class="footer">
  <div class="foot-head" style="left:116px">Quick Links</div>
  <svg class="abs" style="left:110px;top:93px" width="14" height="130" viewBox="0 0 14 130" fill="none" stroke="#1c1c1c" stroke-width="2"><polyline points="4,2 9,6 4,10"/><polyline points="4,33 9,37 4,41"/><polyline points="4,64 9,68 4,72"/><polyline points="4,95 9,99 4,103"/><polyline points="4,125 9,129 4,133"/></svg>
  <span class="foot-link" style="top:90px">Home</span>
  <span class="foot-link" style="top:121px">About Us</span>
  <span class="foot-link" style="top:152px">Gallery</span>
  <span class="foot-link" style="top:183px">Locations</span>
  <span class="foot-link" style="top:213px">Contact Us</span>

  <div class="foot-head" style="left:339px">Contact Us</div>
  <svg class="abs" style="left:340px;top:88px" width="16" height="160" viewBox="0 0 16 160" fill="#1c1c1c">
    <path d="M8 0a6 6 0 0 0-6 6c0 4.5 6 11 6 11s6-6.5 6-11a6 6 0 0 0-6-6zm0 8.3a2.3 2.3 0 1 1 0-4.6 2.3 2.3 0 0 1 0 4.6z"/>
    <path d="M3 64c1 4 5 8 9 9l2-2-3-3-2 1c-1-1-2-2-3-4l1-2-3-3z"/>
    <rect x="2" y="96" width="12" height="12"/>
    <rect x="2" y="144" width="13" height="9"/>
  </svg>
  <div class="contact-item" style="top:89px">420 Orchard Lane<br>Fairview, IL 60000</div>
  <div class="contact-item" style="top:151px">555.014.2280</div>
  <div class="contact-item" style="top:183px">1-555 013 7720</div>
  <div class="contact-item" style="top:228px">hello@maplehollow.org</div>

  <div class="map" role="img" aria-label="Street map showing the farm location"></div>
</footer>

<div class="bottom-bar">
  <span class="social" style="left:110px"></span>
  <span class="social" style="left:156px"></span>
  <span class="social" style="left:202px"></span>
  <span class="social" style="left:248px"></span>
  <span class="copyright">© 2019 &nbsp;|&nbsp; www.maplehollow.org</span>
</div>
<div class="base-line"></div>

</body>
</html>
```